Brenlow Estates Website and Logo Design

We need a new logo and website designed for 'Brenlow Estates Ltd', which is a well established Guernsey property holding company founded in 1934.

The company does not currently have a website. The new website should be similar in style and layout to https://www.quorvanhall.example/.

Target Market(s)

Industry, Media, Tenants

Industry/Entity Type

Property Management

Logo Text

BEL OR Brenlow Estates Ltd OR BE

Coding

Coded - Design and coding required

Number of Pages Required

4 page

Font styles to use
Other font styles liked:
• Helvetica

Requirements
Must have
• The logo laying over the picture (like https://www.quorvanhall.example/).
• Big pictures on homepage (like https://www.quorvanhall.example/)

```html
<!DOCTYPE html>
<html lang="en">
<head>
<meta charset="utf-8">
<title>Brenlow Estates — Blog &amp; Contact</title>
<link rel="stylesheet" href="https://fonts.googleapis.com/css2?family=Lato:wght@300;400;700&display=swap">
<style>
  :root {
    --green: #a6c71c;
    --green-band: #b2d31a;
    --ink: #2f2f2f;
    --muted: #6e6e6e;
    --rule: #e3e3e3;
    --footer: #333333;
    --white: #ffffff;
    --map: #f1f1f1;
  }
  * { box-sizing: border-box; margin: 0; padding: 0; }
  html, body { width: 1200px; height: 1200px; overflow: hidden; background: var(--white); }
  body { font-family: "Lato", Helvetica, Arial, sans-serif; color: var(--ink); position: relative; }

  .blog-grid { position: absolute; top: 0; left: 0; width: 1200px; height: 360px; }
  .blog-card { position: absolute; top: 0; width: 300px; text-align: center; }
  .blog-card__photo { width: 300px; }
  .blog-card--short .blog-card__photo { height: 132px; }
  .blog-card--tall .blog-card__photo { height: 210px; }
  .photo--lounge { background: linear-gradient(160deg, #3f342b 0%, #6b5846 60%, #8a7664 100%); }
  .photo--towers { background: linear-gradient(180deg, #c9dcef 0%, #6d8aab 45%, #2e4560 100%); }
  .photo--pool { background: linear-gradient(180deg, #4a6b3a 0%, #8a7a78 40%, #2e9fd6 100%); }
  .photo--deck { background: linear-gradient(180deg, #5b4a32 0%, #6f6a86 45%, #4d3f5e 100%); }
  .blog-card__title { margin-top: 27px; font-size: 17px; font-weight: 700; letter-spacing: 0; color: var(--ink); }
  .blog-card__text { margin: 16px auto 0; width: 250px; font-size: 12px; line-height: 18px; font-weight: 300; color: var(--muted); }
  .blog-card__link { display: inline-flex; align-items: center; gap: 6px; margin-top: 13px; font-size: 11.5px; font-weight: 400; color: var(--green); text-decoration: none; }

  .contact { position: absolute; top: 0; left: 0; width: 1200px; }
  .contact__title { position: absolute; top: 396px; width: 1200px; text-align: center; font-size: 39px; font-weight: 700; color: var(--ink); letter-spacing: 0.5px; }
  .contact__rule { position: absolute; top: 457px; left: 160px; width: 880px; height: 1px; background: var(--rule); }
  .contact__accent { position: absolute; top: 456px; left: 536px; width: 128px; height: 3px; background: var(--green); }

  .field { position: absolute; left: 338px; width: 524px; font-size: 12px; color: var(--ink); padding-left: 8px; }
  .field--line { height: 40px; border-bottom: 1px solid #4a4a4a; padding-top: 13px; }
  .field--name { top: 488px; }
  .field--email { top: 535px; }
  .field--message { top: 587px; height: 79px; border: 1px solid #4a4a4a; padding-top: 7px; }
  .send-button { position: absolute; top: 692px; left: 535px; width: 131px; height: 30px; border: 1px solid var(--green); background: var(--white); font-family: inherit; font-size: 12px; font-weight: 700; color: var(--ink); line-height: 28px; text-align: center; }

  .map { position: absolute; top: 752px; left: 0; width: 1200px; height: 224px; background: linear-gradient(135deg, #f4f4f4 0%, #ebebeb 50%, #f3f3f3 100%); }
  .map__pin { position: absolute; left: 580px; top: 826px; }

  .site-footer { position: absolute; top: 976px; left: 0; width: 1200px; height: 179px; background: var(--footer); color: var(--white); font-size: 12px; }
  .contact-list { position: absolute; top: 42px; left: 0; width: 1200px; }
  .contact-list__left { position: absolute; right: 615px; text-align: right; line-height: 15px; }
  .contact-list__right { position: absolute; left: 614px; line-height: 15px; }
  .label { color: var(--green); }
  .contact-list .row2 { top: 45px; }
  .footer-link { color: var(--green); text-decoration: none; }
  .social { position: absolute; top: 122px; left: 0; width: 1200px; display: flex; justify-content: center; gap: 18px; }
  .social__dot { width: 12px; height: 12px; border-radius: 50%; background: var(--white); }

  .legal-band { position: absolute; top: 1155px; left: 0; width: 1200px; height: 45px; background: var(--green-band); text-align: center; font-size: 10.5px; line-height: 45px; color: var(--ink); }
</style>
</head>
<body>

<section class="blog-grid" aria-label="Latest posts">
  <article class="blog-card blog-card--short" style="left:0">
    <div class="blog-card__photo photo--lounge" role="img" aria-label="Sun loungers on a wooden pool deck"></div>
    <h3 class="blog-card__title">BLOG TITLE HERE</h3>
    <p class="blog-card__text">Lorem Ipsum is simply dummy text of the prin-ting and typesetting industry.</p>
    <a class="blog-card__link" href="#">LEARN MORE
      <svg width="11" height="9" viewBox="0 0 11 9"><path d="M0 4.5h9M5.5 1l3.5 3.5-3.5 3.5" fill="none" stroke="currentColor" stroke-width="1.6"/></svg></a>
  </article>
  <article class="blog-card blog-card--tall" style="left:300px">
    <div class="blog-card__photo photo--towers" role="img" aria-label="Glass office towers against a blue sky"></div>
    <h3 class="blog-card__title">BLOG TITLE HERE</h3>
    <p class="blog-card__text">Lorem Ipsum is simply dummy text of the prin-ting and typesetting industry.</p>
    <a class="blog-card__link" href="#">LEARN MORE
      <svg width="11" height="9" viewBox="0 0 11 9"><path d="M0 4.5h9M5.5 1l3.5 3.5-3.5 3.5" fill="none" stroke="currentColor" stroke-width="1.6"/></svg></a>
  </article>
  <article class="blog-card blog-card--short" style="left:600px">
    <div class="blog-card__photo photo--pool" role="img" aria-label="Landscaped pool with rocks and palms at dusk"></div>
    <h3 class="blog-card__title">BLOG TITLE HERE</h3>
    <p class="blog-card__text">Lorem Ipsum is simply dummy text of the prin-ting and typesetting industry.</p>
    <a class="blog-card__link" href="#">LEARN MORE
      <svg width="11" height="9" viewBox="0 0 11 9"><path d="M0 4.5h9M5.5 1l3.5 3.5-3.5 3.5" fill="none" stroke="currentColor" stroke-width="1.6"/></svg></a>
  </article>
  <article class="blog-card blog-card--tall" style="left:900px">
    <div class="blog-card__photo photo--deck" role="img" aria-label="Evening terrace deck beside a lit building"></div>
    <h3 class="blog-card__title">BLOG TITLE HERE</h3>
    <p class="blog-card__text">Lorem Ipsum is simply dummy text of the prin-ting and typesetting industry.</p>
    <a class="blog-card__link" href="#">LEARN MORE
      <svg width="11" height="9" viewBox="0 0 11 9"><path d="M0 4.5h9M5.5 1l3.5 3.5-3.5 3.5" fill="none" stroke="currentColor" stroke-width="1.6"/></svg></a>
  </article>
</section>

<section class="contact" aria-labelledby="contact-title">
  <h2 class="contact__title" id="contact-title">CONTACT</h2>
  <div class="contact__rule"></div>
  <div class="contact__accent"></div>
  <div class="field field--line field--name">Your name</div>
  <div class="field field--line field--email">Your Email</div>
  <div class="field field--message">Your message</div>
  <div class="send-button">SEND MESSAGE</div>
</section>

<div class="map" role="img" aria-label="Street map of the office neighbourhood"></div>
<svg class="map__pin" width="33" height="46" viewBox="0 0 33 46" aria-hidden="true">
  <path d="M16.5 0C7.4 0 0 7.2 0 16.2 0 28 16.5 46 16.5 46S33 28 33 16.2C33 7.2 25.6 0 16.5 0z" fill="#1f1f1f"/>
  <circle cx="16.5" cy="15.5" r="5.5" fill="#ffffff"/>
</svg>

<footer class="site-footer">
  <div class="contact-list">
    <div class="contact-list__left">
      <div><span class="label">Telephone:</span> 000 555 0142</div>
      <div><span class="label">Fax:</span> 000 555 0142</div>
    </div>
    <div class="contact-list__right">
      <div>14 Harbour Lane</div>
      <div>Glass Tower, St Peter Port</div>
    </div>
  </div>
  <div class="contact-list" style="top:87px">
    <div class="contact-list__left"><span class="label">E-mail:</span> info@brenlowestates.example</div>
    <div class="contact-list__right"><a class="footer-link" href="#">Get Directions</a></div>
  </div>
  <div class="social" aria-label="Social links">
    <span class="social__dot"></span><span class="social__dot"></span><span class="social__dot"></span>
  </div>
</footer>

<div class="legal-band">© 2016 — Brenlow Estates Limited</div>

</body>
</html>
```